Elevating our current Business Card Design

We want to elevate our current business card with a new design to look like a zenith 300 company. We are a premium lubricant distributor (oil and grease).
We need 2 versions, version 1 is as per the uploaded a copy of our current business card with the English version.
For our Chinese version we need to use the front to be English in English and have the back of the card designed exactly like the front for all info to be in Chinese.
The design template needs to be such that we can amend the template with adding different information for each person's card.
The background colour of the card can be changed- we just need to clearly see all information on the card and logos.
The QJR and Ember steady logos cannot have any colour or display changes- only use the logos attached.
All logos need to be included and all information from the attached current card

```html
<!DOCTYPE html>
<html lang="en">
<head>
<meta charset="utf-8">
<title>Orbis Lubricant Traders – Business Card</title>
<link rel="stylesheet" href="https://fonts.googleapis.com/css2?family=Open+Sans:ital,wght@0,400;0,600;0,700;0,800;1,800&display=swap">
<style>
  :root {
    --stage: #1e1e20;
    --card: #1f1f23;
    --red: #e5262a;
    --red-deep: #8e1519;
    --gold: #f0b429;
    --gold-deep: #d89a1c;
    --white: #ffffff;
    --grey: #b9b9bd;
    --orange: #e8671c;
  }
  * { margin: 0; padding: 0; box-sizing: border-box; }
  html, body {
    width: 1200px; height: 780px; overflow: hidden;
    background: var(--stage);
    font-family: "Open Sans", Arial, sans-serif;
  }
  .card {
    position: absolute; top: 230px;
    width: 520px; height: 320px;
    border-radius: 22px; overflow: hidden;
    background: var(--card);
    box-shadow: 0 18px 40px rgba(0,0,0,.55);
  }
  .card--front { left: 50px; }
  .card--back { left: 630px; }
  .card__art { position: absolute; inset: 0; }

  /* brand name used in place of the mark */
  .brand {
    position: absolute; display: flex; align-items: center; gap: 10px;
    color: var(--red); font-weight: 800; letter-spacing: 2px; line-height: 1;
  }
  .brand__dot { border-radius: 50%; background: var(--gold); flex: none; }
  .card--front .brand { left: 38px; top: 40px; font-size: 44px; }
  .card--front .brand__dot { width: 16px; height: 16px; }
  .card--back .brand { left: 150px; top: 90px; font-size: 86px; }
  .card--back .brand__dot { width: 26px; height: 26px; }

  .holder { position: absolute; right: 28px; top: 44px; text-align: right; }
  .holder__name { color: var(--red); font-size: 28px; font-weight: 800; font-style: italic; line-height: 1.1; }
  .holder__role { color: var(--white); font-size: 14px; margin-top: 2px; }

  .contact { position: absolute; right: 26px; top: 160px; text-align: right; color: var(--white); font-size: 13px; line-height: 20px; }
  .contact__address { margin-bottom: 8px; }
  .contact__row { display: flex; justify-content: flex-end; align-items: center; gap: 8px; }
  .contact__icon { width: 14px; height: 14px; flex: none; }

  .badges {
    position: absolute; left: 22px; right: 22px; bottom: 24px;
    display: flex; align-items: center; gap: 14px;
  }
  .badge-ember { color: var(--white); font-size: 13px; font-weight: 700; line-height: 1.05; }
  .badge-cert {
    width: 34px; height: 34px; border-radius: 50%;
    background: var(--orange); border: 3px solid var(--grey); flex: none;
  }
  .partner { display: flex; height: 40px; border: 2px solid var(--red); }
  .partner__own { display: flex; align-items: center; gap: 6px; padding: 0 10px; color: var(--white); font-size: 8px; font-weight: 600; line-height: 1.15; }
  .partner__own-name { color: var(--red); font-size: 15px; font-weight: 800; letter-spacing: 1px; }
  .partner__corvane { background: var(--red); color: var(--white); padding: 5px 12px; font-size: 15px; font-weight: 800; line-height: 1; }
  .partner__corvane small { display: block; font-size: 7px; font-weight: 600; letter-spacing: 1px; margin-top: 3px; }
</style>
</head>
<body>

<section class="card card--front" aria-label="Card front">
  <svg class="card__art" viewBox="0 0 520 320" aria-hidden="true">
    <defs>
      <linearGradient id="redWave" x1="0" y1="0" x2="1" y2="1">
        <stop offset="0" stop-color="#e5262a"/>
        <stop offset="1" stop-color="#8e1519"/>
      </linearGradient>
      <linearGradient id="goldWave" x1="0" y1="0" x2="1" y2="0">
        <stop offset="0" stop-color="#f0b429"/>
        <stop offset="1" stop-color="#d89a1c"/>
      </linearGradient>
    </defs>
    <path d="M0,262 C150,175 320,222 520,84 L520,320 L0,320 Z" fill="#c41f24"/>
    <path d="M0,268 C150,181 320,228 520,90 L520,320 L0,320 Z" fill="#1f1f23"/>
    <path d="M0,274 C150,187 320,234 520,96 L520,320 L0,320 Z" fill="url(#goldWave)"/>
    <path d="M0,286 C150,199 320,246 520,108 L520,320 L0,320 Z" fill="#1f1f23"/>
    <path d="M0,290 C150,203 320,250 520,112 L520,320 L0,320 Z" fill="url(#redWave)"/>
  </svg>

  <div class="brand"><span>ORBIS</span><span class="brand__dot"></span></div>

  <div class="holder">
    <p class="holder__name">Marina Castell</p>
    <p class="holder__role">Administration Executive</p>
  </div>

  <div class="contact">
    <p class="contact__address">48 Freightway Drive<br>Lindale, WA 6190</p>
    <p class="contact__row">1300 000 412
      <svg class="contact__icon" viewBox="0 0 16 16"><path d="M3 1l3 3-2 2c1 2 3 4 5 5l2-2 3 3-2 3C7 15 1 9 1 3z" fill="#f0b429"/></svg></p>
    <p class="contact__row">+61 400 123 456
      <svg class="contact__icon" viewBox="0 0 16 16"><rect x="4" y="1" width="8" height="14" rx="1.5" fill="none" stroke="#f0b429" stroke-width="1.6"/></svg></p>
    <p class="contact__row">+61 8 9000 4521
      <svg class="contact__icon" viewBox="0 0 16 16"><rect x="1" y="6" width="14" height="9" rx="1" fill="#f0b429"/><rect x="4" y="1" width="8" height="5" fill="#f0b429"/></svg></p>
    <p class="contact__row">www.orbislube.com
      <svg class="contact__icon" viewBox="0 0 16 16"><circle cx="8" cy="8" r="6.5" fill="none" stroke="#f0b429" stroke-width="1.6"/><path d="M1.5 8h13M8 1.5c-3 3-3 10 0 13M8 1.5c3 3 3 10 0 13" fill="none" stroke="#f0b429" stroke-width="1.2"/></svg></p>
    <p class="contact__row">m.castell@orbislube.com
      <svg class="contact__icon" viewBox="0 0 16 16"><rect x="1" y="3" width="14" height="10" rx="1" fill="#f0b429"/><path d="M1.5 3.5L8 9l6.5-5.5" fill="none" stroke="#8e1519" stroke-width="1.4"/></svg></p>
  </div>
</section>

<section class="card card--back" aria-label="Card back">
  <div class="brand"><span>ORBIS</span><span class="brand__dot"></span></div>

  <div class="badges">
    <p class="badge-ember">Ember<br>steady</p>
    <span class="badge-cert" role="img" aria-label="QJR certification badge"></span>
    <div class="partner">
      <div class="partner__own"><span class="partner__own-name">ORBIS</span><span>ORBIS LUBRICANT<br>TRADERS</span></div>
      <p class="partner__corvane">CORVANE<small>PREMIUM LUBRICANTS</small></p>
    </div>
    <span class="badge-cert" role="img" aria-label="QJR certification badge"></span>
    <span class="badge-cert" role="img" aria-label="QJR certification badge"></span>
  </div>
</section>

</body>
</html>
```